New Bicycle shop business card

Hi!
I'm looking for a business card for my new proffesional bike mechanics shop. This shop is only for fixing broken bikes and not selling bikes.
Peferbly a modern and sleek and modern design.
Colors: black, grey, red, white
Information:
Name: Rijwielwerkplaats Vanhoutte
Shop owner: Bart Vanhoutte & Marieke Segers
Website: www.rijwielwerkplaats-vanhoutte.be
Email: info@rijwielwerkplaats-vanhoutte.be
Phone number: +32471902368
Street adres: Kerkweg 46
9940 Bellebeke
Slogan/shop information: Herstellingen van alle merken.
Logo: see files.
Target Market(s)
People who seek a mechanic to fix or upgrade their bikes.
Contact Information for Business Card
Information:
Website: info@rijwielwerkplaats-vanhoutte.be
9940 Bellebeke
Logo: see files.

```html
<!DOCTYPE html>
<html lang="nl">
<head>
<meta charset="utf-8">
<title>Rijwielwerkplaats Vanhoutte – Visitekaartje</title>
<link rel="stylesheet" href="https://fonts.googleapis.com/css2?family=Lato:wght@400;700;900&display=swap">
<style>
  :root {
    --bg: #2b2b2b;
    --paper: #ffffff;
    --red: #e0293b;
    --ink: #1d1717;
    --text: #3c3c3c;
    --grey: #a8a8a8;
    --rule: #c9c9c9;
  }
  * { box-sizing: border-box; margin: 0; padding: 0; }
  html, body {
    width: 1200px; height: 1200px; overflow: hidden;
    background: var(--bg);
    font-family: "Lato", Arial, sans-serif;
  }
  .stage { position: relative; width: 1200px; height: 1200px; }

  .card {
    position: absolute; top: 310px; height: 594px;
    box-shadow: 0 6px 14px rgba(0,0,0,.45);
    overflow: hidden;
  }
  .card--front { left: 234px; width: 364px; background: var(--paper); text-align: center; }
  .card--back  { left: 627px; width: 369px; background: var(--red); }

  /* front */
  .brand-dot {
    position: absolute; left: 144px; top: 88px;
    width: 76px; height: 76px; border-radius: 50%;
    background: var(--red);
  }
  .brand-name {
    position: absolute; left: 0; right: 0; top: 186px;
    font-weight: 900; font-size: 27px; line-height: 32px;
    letter-spacing: 1px; text-transform: uppercase; color: var(--ink);
  }
  .owners {
    position: absolute; left: 0; right: 0; top: 340px;
    font-weight: 700; font-size: 17px; color: var(--red);
    text-transform: uppercase;
  }
  .role { position: absolute; left: 0; right: 0; top: 360px; font-size: 17px; color: var(--text); }
  .icon-row { position: absolute; left: 86px; top: 396px; width: 192px; height: 24px; }
  .contact {
    position: absolute; left: 0; right: 0; top: 431px;
    font-size: 17px; line-height: 22px; color: var(--text);
  }
  .divider {
    position: absolute; left: 88px; width: 188px; top: 507px;
    border-top: 1px solid var(--rule);
  }
  .address {
    position: absolute; left: 0; right: 0; top: 517px;
    font-size: 17px; line-height: 22px; color: var(--text);
  }

  /* back */
  .back-band { position: absolute; left: 0; top: 0; }
  .back-name {
    position: absolute; left: 0; right: 0; top: 250px;
    text-align: center; color: var(--paper);
    font-weight: 900; font-size: 30px; line-height: 38px;
    letter-spacing: 1px; text-transform: uppercase;
  }
  .back-url {
    position: absolute; left: 0; right: 0; top: 532px;
    text-align: center; color: var(--paper); font-size: 19px;
  }
</style>
</head>
<body>
<main class="stage">
  <section class="card card--front">
    <div class="brand-dot"></div>
    <h1 class="brand-name">Rijwielwerkplaats<br>Vanhoutte</h1>

    <p class="owners">Bart Vanhoutte &amp; Marieke Segers</p>
    <p class="role">Owner</p>

    <svg class="icon-row" viewBox="0 0 192 24" aria-hidden="true">
      <line x1="0" y1="12" x2="54" y2="12" stroke="#9a9a9a" stroke-width="1.2"/>
      <line x1="138" y1="12" x2="192" y2="12" stroke="#9a9a9a" stroke-width="1.2"/>
      <g fill="var(--red)">
        <circle cx="68" cy="12" r="12"/><circle cx="96" cy="12" r="12"/><circle cx="124" cy="12" r="12"/>
      </g>
      <!-- phone -->
      <path d="M62 9c0-2 2-3 6-3s6 1 6 3l-2 1c0-1-1-2-4-2s-4 1-4 2z M63 15h10v3H63z M66 11h4l2 4h-8z" fill="#fff"/>
      <!-- mail -->
      <rect x="89" y="7" width="14" height="10" fill="#fff"/>
      <path d="M89 7l7 6 7-6" fill="none" stroke="var(--red)" stroke-width="1.3"/>
      <!-- globe -->
      <circle cx="124" cy="12" r="6.5" fill="#fff"/>
      <path d="M124 5.5v13M117.5 12h13M124 5.5c-3 3-3 10 0 13M124 5.5c3 3 3 10 0 13" fill="none" stroke="var(--red)" stroke-width="1"/>
    </svg>

    <p class="contact">+32471902368<br>info@rijwielwerkplaats-vanhoutte.be<br>www.rijwielwerkplaats-vanhoutte.be</p>
    <div class="divider"></div>
    <p class="address">Kerkweg 46<br>9940 Bellebeke</p>
  </section>

  <section class="card card--back">
    <svg class="back-band" width="369" height="130" viewBox="0 0 369 130" aria-hidden="true">
      <path d="M0 0H369V118Q184 92 0 114Z" fill="var(--grey)"/>
    </svg>
    <p class="back-name">Rijwielwerkplaats<br>Vanhoutte</p>
    <p class="back-url">www.rijwielwerkplaats-vanhoutte.be</p>
  </section>
</main>
</body>
</html>
```